KLV Plant Services

We are a heavy diesel mechanical business with additional air con certificates, remapping engine rebuilt

Contact Information for Business Card

Company Name, Director Name, Managing Director, Contact details, email and website

Font styles to use
Serif
Script

```html
<!DOCTYPE html>
<html lang="en">
<head>
<meta charset="utf-8">
<title>KLV Plant Services – Business Card</title>
<link href="https://fonts.googleapis.com/css2?family=Arimo:wght@400;700&family=Libre+Baskerville:wght@400;700&display=swap" rel="stylesheet">
<style>
  :root {
    --stage: #2e2e2e;
    --card-dark: #161616;
    --mark-dark: #8c8c8c;
    --card-light: #ffffff;
    --navy: #0f0f6e;
    --ink: #1c1c1c;
    --white: #ffffff;
    --serif: "Libre Baskerville", Georgia, serif;
    --sans: "Arimo", Arial, sans-serif;
  }
  * { box-sizing: border-box; margin: 0; padding: 0; }
  html, body { width: 1200px; height: 875px; overflow: hidden; }
  body {
    background: var(--stage);
    font-family: var(--sans);
    position: relative;
  }
  .card {
    position: absolute;
    top: 283px;
    width: 540px;
    height: 309px;
    border-radius: 18px;
    overflow: hidden;
  }
  .card--front { left: 40px; background: var(--card-dark); }
  .card--back { left: 620px; background: var(--card-light); }

  .brand {
    position: absolute;
    display: flex;
    align-items: center;
    gap: 12px;
    font-family: var(--serif);
    font-weight: 700;
    white-space: nowrap;
  }
  .brand__dot { border-radius: 50%; flex: none; }

  .card--front .brand {
    left: 50%; top: 50%;
    transform: translate(-50%, -50%);
    color: var(--mark-dark);
    font-size: 32px;
  }
  .card--front .brand__dot { width: 32px; height: 32px; border: 3px solid var(--mark-dark); }

  .card--back .brand {
    right: 26px; top: 36px;
    color: var(--navy);
    font-size: 18px;
    gap: 8px;
  }
  .card--back .brand__dot { width: 20px; height: 20px; border: 2px solid var(--navy); }

  .band { position: absolute; left: 0; top: 0; width: 540px; height: 309px; }

  .person {
    position: absolute;
    left: 40px; top: 112px;
    color: var(--white);
  }
  .person__name { font-family: var(--serif); font-size: 23px; font-weight: 700; letter-spacing: 0.5px; }
  .person__role { font-size: 15px; margin-top: 6px; }

  .company {
    position: absolute;
    right: 26px; top: 196px;
    text-align: right;
    font-size: 13px;
    line-height: 1.45;
    color: var(--ink);
  }
  .company__name { font-family: var(--serif); color: var(--navy); font-weight: 700; font-size: 13px; }

  .contacts {
    position: absolute;
    left: 40px; top: 200px;
    list-style: none;
    font-size: 14px;
    color: var(--ink);
  }
  .contacts li { display: flex; align-items: center; gap: 10px; height: 22px; }
  .contacts svg { width: 13px; height: 13px; fill: var(--navy); flex: none; }
</style>
</head>
<body>

<section class="card card--front" aria-label="Card front">
  <div class="brand"><span class="brand__dot"></span>KLV Plant Services</div>
</section>

<section class="card card--back" aria-label="Card back">
  <svg class="band" viewBox="0 0 540 309" aria-hidden="true">
    <polygon points="0,82 395,82 315,182 0,182" fill="var(--navy)"/>
  </svg>

  <div class="brand"><span class="brand__dot"></span>KLV Plant Services</div>

  <div class="person">
    <p class="person__name">DANIEL HARPER</p>
    <p class="person__role">Managing Director</p>
  </div>

  <div class="company">
    <p class="company__name">KLV PLANT SERVICES</p>
    <p>27 Foundry Road, Millbrook, State</p>
    <p>Country, Zip Code 40718</p>
    <p>www.klvplantservices.com</p>
  </div>

  <ul class="contacts">
    <li><svg viewBox="0 0 16 16"><path d="M3 1l3 3-1.5 2a9 9 0 0 0 5.5 5.5L12 10l3 3-2 2C6 15 1 10 1 3z"/></svg>(555) 210-4730</li>
    <li><svg viewBox="0 0 16 16"><path d="M4 0h8a1 1 0 0 1 1 1v14a1 1 0 0 1-1 1H4a1 1 0 0 1-1-1V1a1 1 0 0 1 1-1zm1 2v10h6V2z"/></svg>(555) 210-4731</li>
    <li><svg viewBox="0 0 16 16"><path d="M4 0h8v4H4zM1 5h14v7h-3v4H4v-4H1zm5 6v3h4v-3z"/></svg>(555) 210-4732</li>
    <li><svg viewBox="0 0 16 16"><path d="M0 3h16v10H0zm1.5 1.5L8 9l6.5-4.5z" fill-rule="evenodd"/></svg>info@klvplantservices.com</li>
  </ul>
</section>

</body>
</html>
```